Executive Business Card for Healthcare Company [Need Today]

I need a business card design for a healthcare company. The only branding the company has thus far is a logo. The cards will be utilized by company executives. The design I envision will be vibrant and appealing but with a corporate feel. They shouldn't be too casual or playful. I would like to complete this project TODAY if possible.

Target Market(s)

Healthcare vendors, other executives in healthcare and pharmaceuticals

Industry/Entity Type

Pharmaceutical

Contact Information for Business Card

See attachment

Font styles to use
Serif
Sans Serif

Colors

Designer to choose colors to be used in the design.

```html
<!DOCTYPE html>
<html lang="en">
<head>
<meta charset="UTF-8">
<title>Veridan Therapeutics — Business Card</title>
<link href="https://fonts.googleapis.com/css2?family=Roboto:wght@300;400;500;700&display=swap" rel="stylesheet">
<style>
  :root {
    --stage: #2e2e2e;
    --card: #111111;
    --silver: #dcdcdc;
    --silver-soft: #a9a9a9;
    --emboss: #2c2c2c;
    --emboss-line: #3a3a3a;
    --rule: #6e6e6e;
  }
  * { margin: 0; padding: 0; box-sizing: border-box; }
  html, body { width: 1200px; height: 900px; overflow: hidden; }
  body {
    background: var(--stage);
    font-family: "Roboto", Arial, sans-serif;
    display: flex;
    flex-direction: column;
    align-items: center;
    justify-content: center;
    gap: 56px;
  }
  .card {
    width: 630px;
    height: 360px;
    background: var(--card);
    border-radius: 28px;
    position: relative;
    overflow: hidden;
  }

  /* Brand side */
  .brand-side {
    display: flex;
    align-items: center;
    justify-content: center;
    gap: 26px;
  }
  .brand-mark {
    width: 96px; height: 96px;
    border-radius: 50%;
    border: 2px solid var(--emboss-line);
  }
  .brand-divider {
    width: 1px; height: 110px;
    background: var(--rule);
  }
  .brand-name {
    font-size: 40px;
    font-weight: 300;
    color: var(--silver);
    letter-spacing: 1px;
    line-height: 1.1;
  }

  /* Contact side */
  .contact-side .brand-lockup {
    position: absolute;
    left: 46px; top: 70px;
    display: flex; align-items: center; gap: 16px;
  }
  .contact-side .brand-mark { width: 64px; height: 64px; }
  .contact-side .brand-name {
    font-size: 24px;
    color: var(--emboss-line);
    width: 150px;
  }
  .contact-divider {
    position: absolute;
    left: 290px; top: 150px;
    width: 1px; height: 160px;
    background: var(--rule);
  }
  .contact-block {
    position: absolute;
    left: 318px; top: 150px;
    color: var(--silver-soft);
    font-size: 15px;
    line-height: 1.45;
  }
  .person-name {
    font-size: 26px;
    font-weight: 700;
    color: var(--silver);
    line-height: 1.1;
  }
  .person-title { color: var(--silver-soft); margin-bottom: 2px; }
  .contact-row { display: flex; align-items: center; gap: 8px; }
  .contact-row svg { width: 13px; height: 13px; fill: none; stroke: var(--silver-soft); stroke-width: 1.6; }
</style>
</head>
<body>

  <section class="card brand-side">
    <div class="brand-mark"></div>
    <div class="brand-divider"></div>
    <div class="brand-name">Veridan<br>Therapeutics</div>
  </section>

  <section class="card contact-side">
    <div class="brand-lockup">
      <div class="brand-mark"></div>
      <div class="brand-name">Veridan Therapeutics</div>
    </div>
    <div class="contact-divider"></div>
    <div class="contact-block">
      <div class="person-name">Martin Hale</div>
      <div class="person-title">Senior Director of Marketing</div>
      <div>Veridan Therapeutics, LLC</div>
      <div>118 W Laurel Avenue</div>
      <div>Dalton, GA 30720</div>
      <div class="contact-row">
        <svg viewBox="0 0 16 16"><path d="M3 2h3l1.5 3.5-2 1.2a8 8 0 0 0 3.8 3.8l1.2-2L14 10v3a1 1 0 0 1-1 1A11 11 0 0 1 2 3a1 1 0 0 1 1-1z"/></svg>
        <span>555-214-0387</span>
      </div>
      <div class="contact-row">
        <svg viewBox="0 0 16 16"><rect x="4" y="1.5" width="8" height="13" rx="1.5"/><path d="M7 12.5h2"/></svg>
        <span>555-382-6140</span>
      </div>
      <div class="contact-row">
        <svg viewBox="0 0 16 16"><rect x="1.5" y="3.5" width="13" height="9" rx="1"/><path d="M1.5 4l6.5 5 6.5-5"/></svg>
        <span>mhale@veridanrx.com</span>
      </div>
    </div>
  </section>

</body>
</html>
```